BOLD & MINIMALIST DESIGN NEEDED

We want a very bold but minimalistic business card design that is impactful and utilizes both sides of the business card. Our current logo is included for your use.

We want bold fonts and good use of negative space. We don't want the logo to overpower the design.

Target Market(s)

Professionals who are building new commercial buildings.

Industry/Entity Type

Construction

Contact Information for Business Card

Name, Title, email, office phone, cell phone, website

Font styles to use
Serif
Sans Serif

Requirements
Must have
• Bold design!

```html
<!DOCTYPE html>
<html lang="en">
<head>
<meta charset="utf-8">
<title>Ridgeline Design + Build — Business Card</title>
<link href="https://fonts.googleapis.com/css2?family=Montserrat:wght@400;500;800&family=Oswald:wght@700&display=swap" rel="stylesheet">
<style>
  :root {
    --backdrop: #d2d3ce;
    --card: #121212;
    --accent: #7dc242;
    --ink: #ffffff;
    --ghost: #242424;
  }
  * { margin: 0; padding: 0; box-sizing: border-box; }
  html, body { width: 1200px; height: 801px; overflow: hidden; }
  body {
    background: var(--backdrop);
    font-family: "Montserrat", sans-serif;
    position: relative;
  }
  .card {
    position: absolute;
    top: 246px;
    width: 540px;
    height: 309px;
    background: var(--card);
    border-bottom: 4px solid var(--accent);
    box-shadow: 0 18px 30px rgba(0,0,0,.25);
    overflow: hidden;
  }
  .card--front { left: 40px; }
  .card--back { left: 620px; }

  .wordmark { position: absolute; left: 34px; top: 46px; color: var(--ink); z-index: 1; }
  .wordmark__name {
    font-weight: 800; font-size: 34px; letter-spacing: 1px; line-height: 1;
    white-space: nowrap;
  }
  .wordmark__tag {
    margin-top: 6px; font-weight: 500; font-size: 10px; letter-spacing: 7px;
    padding-left: 50px; white-space: nowrap;
  }

  .monogram {
    position: absolute; right: 28px; top: 150px;
    font-weight: 800; font-size: 36px; line-height: 1; color: var(--ghost);
    letter-spacing: 1px; white-space: nowrap;
  }

  .person { position: absolute; left: 34px; top: 150px; z-index: 1; }
  .person__name {
    font-family: "Oswald", sans-serif; font-weight: 700; font-size: 30px;
    color: var(--accent); text-transform: uppercase; line-height: 1;
    white-space: nowrap;
  }
  .person__title {
    margin-top: 4px; font-size: 12px; letter-spacing: 1px; color: var(--ink);
  }

  .contacts { position: absolute; left: 34px; top: 212px; list-style: none; }
  .contacts li {
    display: flex; align-items: center; gap: 8px;
    font-size: 12px; color: var(--ink); line-height: 19px; white-space: nowrap;
  }
  .contacts svg { width: 11px; height: 11px; flex: none; }
  .contacts .hl { color: var(--accent); }

  .pattern {
    position: absolute; inset: 0;
    background: linear-gradient(200deg, #3a3a3a 0%, #1c1c1c 45%, #101010 100%);
  }
  .back-mark {
    position: absolute; left: 0; right: 0; top: 136px; text-align: center;
    font-weight: 800; font-size: 26px; letter-spacing: 1px; color: var(--ink);
  }
</style>
</head>
<body>
  <section class="card card--front">
    <div class="wordmark">
      <div class="wordmark__name">RIDGELINE</div>
      <div class="wordmark__tag">DESIGN + BUILD</div>
    </div>
    <div class="monogram" aria-hidden="true">RIDGELINE</div>

    <div class="person">
      <div class="person__name">Mark Ellison</div>
      <div class="person__title">OWNER</div>
    </div>

    <ul class="contacts">
      <li>
        <svg viewBox="0 0 12 12"><path d="M2 1l2 0 1 3-1.5 1a6 6 0 0 0 3.5 3.5L8 7l3 1v2a1 1 0 0 1-1 1A9 9 0 0 1 1 2a1 1 0 0 1 1-1z" fill="var(--accent)"/></svg>
        (555) 214-7360
      </li>
      <li>
        <svg viewBox="0 0 12 12"><rect x="1" y="4" width="10" height="7" rx="1.5" fill="var(--accent)"/><path d="M1 4c1-3 9-3 10 0" stroke="var(--accent)" stroke-width="1.5" fill="none"/></svg>
        (555) 214-7361
      </li>
      <li>
        <svg viewBox="0 0 12 12"><rect x="1" y="2.5" width="10" height="7" fill="none" stroke="var(--accent)" stroke-width="1.2"/><path d="M1 2.5l5 4 5-4" fill="none" stroke="var(--accent)" stroke-width="1.2"/></svg>
        ridgelinebuild@mail.com
      </li>
      <li>
        <svg viewBox="0 0 12 12"><circle cx="6" cy="6" r="5" fill="none" stroke="var(--accent)" stroke-width="1.2"/><path d="M1 6h10M6 1c-3 3-3 7 0 10M6 1c3 3 3 7 0 10" fill="none" stroke="var(--accent)" stroke-width="1"/></svg>
        <span>www.<span class="hl">ridgelinebuild</span>.com</span>
      </li>
    </ul>
  </section>

  <section class="card card--back">
    <div class="pattern" role="img" aria-label="Repeating tonal brand pattern in dark greys across the card"></div>
    <div class="back-mark">RIDGELINE</div>
  </section>
</body>
</html>
```